International business needs business cards

Our company, DRV Ventures Inc. is in the business of supplying a range construction products with particular emphasis on CEMENT. We have developed our own brand - TORVAN SUPPLIES - with which to infiltrate the market. We are launching our brand of cement (TORVAN Type IS Cement) into the Caribbean which is unlike anything this market has ever seen. A monopoly has existed here for the past 60-odd years and the market has now opened to allow the importation of other brands and consumers are anxious and ready for change/improvement. We are very excited to be launching and want to make a great first impression. We will be conducting workshops and seminars (from government level to the hardware store owners) and we want our business card to give us the strong, confident introduction that we need.

Target Market(s)

construction; builders; engineers; home owners

Industry/Entity Type

Construction

Contact Information for Business Card

Marisol Depree
CEO
cell # 1 555 4180736
Ground floor,Lindell Plaza Suite 2734
George Town,Grand Cayman
Cayman Islands,KY1-4823
EMAIL: m.depree@drvventuresinc.example
web site drvventuresinc.example

COMPANY: skype info drv.ventures.example

second card
Yvette Brannock-Depree
CFO
CELL# 1 555 607 3941
George Town,Grand Cayman
Cayman Islands,KY1-4823
EMAIL: y.brannockdepree@drvventuresinc.example
website drvventuresinc.example

Requirements
Must have
• Business cards must display BOTH logos - DRV is the company and TORVAN is the brand.

```html
<!DOCTYPE html>
<html lang="en">
<head>
<meta charset="utf-8">
<title>DRV Ventures Inc. — Business Card</title>
<link href="https://fonts.googleapis.com/css2?family=Arimo:wght@400;700&display=swap" rel="stylesheet">
<style>
  :root{
    --maroon:#8e1b20;
    --maroon-dark:#6e1216;
    --ink:#2a2a2a;
    --grey:#55585c;
    --rule:#3a3a3a;
    --paper:#ffffff;
    --paper-shade:#e4e4e4;
    --backdrop:#ece9e4;
  }
  *{box-sizing:border-box;margin:0;padding:0}
  html,body{width:1200px;height:950px;overflow:hidden}
  body{
    background:var(--backdrop);
    font-family:"Arimo",Arial,sans-serif;
    color:var(--grey);
    display:flex;flex-direction:column;align-items:center;justify-content:center;gap:44px;
  }
  .card{
    position:relative;width:740px;height:420px;
    background:linear-gradient(135deg,var(--paper) 0%,var(--paper) 45%,var(--paper-shade) 100%);
    box-shadow:0 6px 18px rgba(0,0,0,.18);
    overflow:hidden;
  }
  /* ---------- back ---------- */
  .card-back .brand-mark{
    position:absolute;left:70px;top:120px;width:190px;height:150px;
    display:flex;flex-direction:column;align-items:center;justify-content:center;gap:12px;
  }
  .brand-mark .dot{width:64px;height:64px;border-radius:50%;background:var(--ink)}
  .brand-mark .name{font-size:28px;font-weight:700;letter-spacing:3px;color:var(--ink)}
  .company-mark{display:flex;align-items:center;gap:14px}
  .company-mark .square{width:78px;height:78px;background:var(--maroon)}
  .company-mark .name{font-size:30px;font-weight:700;color:var(--ink);line-height:1.05}
  .card-back .company-mark{position:absolute;left:330px;top:150px}
  .card-back .site{position:absolute;left:0;right:0;bottom:70px;text-align:center;font-size:17px;color:var(--grey);letter-spacing:.5px}
  /* ---------- front ---------- */
  .card-front .accent-bar{position:absolute;left:0;top:130px;width:20px;height:180px;background:var(--maroon)}
  .card-front .company-mark{position:absolute;right:50px;top:50px}
  .card-front .company-mark .square{width:84px;height:84px}
  .person{position:absolute;left:44px;top:132px}
  .person .name{font-size:27px;font-weight:400;color:var(--maroon-dark)}
  .person .title{font-size:15px;color:var(--ink);margin-top:4px}
  .address{position:absolute;left:44px;top:218px;font-size:17px;line-height:1.4;color:var(--grey)}
  .divider{position:absolute;left:385px;top:250px;width:2px;height:96px;background:var(--rule)}
  .contacts{position:absolute;left:405px;top:250px;font-size:17px;line-height:1.55;color:var(--grey);list-style:none}
  .contacts .label{color:var(--maroon);display:inline-block;width:36px}
</style>
</head>
<body>
  <section class="card card-back" aria-label="Card back">
    <div class="brand-mark">
      <span class="dot"></span>
      <span class="name">TORVAN</span>
    </div>
    <div class="company-mark">
      <span class="square"></span>
      <span class="name">DRV Ventures Inc.</span>
    </div>
    <p class="site">drvventuresinc.example</p>
  </section>

  <section class="card card-front" aria-label="Card front">
    <div class="accent-bar"></div>
    <div class="company-mark">
      <span class="square"></span>
      <span class="name">DRV Ventures Inc.</span>
    </div>
    <div class="person">
      <p class="name">Marisol Depree</p>
      <p class="title">CEO</p>
    </div>
    <address class="address" style="font-style:normal">
      Ground floor<br>
      Lindell Plaza Suite 2734<br>
      George Town,Grand Cayman<br>
      Cayman Islands,KY1-4823
    </address>
    <div class="divider"></div>
    <ul class="contacts">
      <li><span class="label">M :</span>1 555 4180736</li>
      <li><span class="label">E :</span>m.depree@drvventuresinc.example</li>
      <li><span class="label">W :</span>drvventuresinc.example</li>
    </ul>
  </section>
</body>
</html>
```